Tech business card design

We need an amazing business card design for our new business 'Pexla' a marketing tech startup based in Sydney, Australia. We provide an online marketplace for businesses to search and buy advertising media, connect with service providers and learn more about marketing. We wish to communicate 'cool tech', reliability and professionalism and design based around our logo.

Target Market(s)

Business Owners

Contact Information for Business Card

Name
Position
Email Address
Website
Phone Number

Font styles to use
Other font styles liked:
• Avenir & Avenir Next

Colors

Designer to choose colors to be used in the design.

```html
<!DOCTYPE html>
<html lang="en">
<head>
<meta charset="UTF-8">
<title>Pexla Business Card</title>
<link href="https://fonts.googleapis.com/css2?family=Nunito+Sans:wght@400;800&display=swap" rel="stylesheet">
<style>
  :root {
    --navy: #1f1d4f;
    --navy-deep: #1a1946;
    --ink: #2a2856;
    --paper: #ffffff;
    --backdrop: #d4d4d6;
    --muted: #4a4870;
  }
  * { margin: 0; padding: 0; box-sizing: border-box; }
  html, body { width: 1200px; height: 900px; overflow: hidden; }
  body {
    background: var(--backdrop);
    font-family: "Nunito Sans", sans-serif;
    display: flex;
    flex-direction: column;
    align-items: center;
    justify-content: center;
    gap: 56px;
  }
  .card {
    width: 640px;
    height: 366px;
    border-radius: 3px;
    box-shadow: 0 10px 28px rgba(0,0,0,0.18);
    position: relative;
  }
  .card-front {
    background: var(--paper);
    color: var(--ink);
    padding: 44px 56px;
    display: flex;
    flex-direction: column;
    justify-content: space-between;
  }
  .wordmark {
    font-weight: 800;
    color: var(--navy);
    letter-spacing: -1px;
    line-height: 1;
  }
  .card-front .wordmark { font-size: 128px; }
  .details {
    display: flex;
    align-items: center;
    gap: 22px;
  }
  .identity { text-align: right; }
  .identity .name { font-weight: 800; font-size: 20px; color: var(--navy); }
  .identity .role { font-weight: 400; font-size: 18px; color: var(--muted); }
  .divider { width: 1.5px; height: 78px; background: var(--ink); }
  .contacts { list-style: none; display: flex; flex-direction: column; gap: 4px; }
  .contacts li {
    display: flex; align-items: center; gap: 10px;
    font-size: 19px; color: var(--ink);
  }
  .contacts svg { width: 16px; height: 16px; flex: none; }
  .card-back {
    background: var(--navy-deep);
    display: flex;
    flex-direction: column;
    align-items: center;
    justify-content: center;
    gap: 14px;
  }
  .card-back .wordmark { color: var(--paper); font-size: 56px; }
  .card-back .site { color: #d9d8ea; font-size: 16px; letter-spacing: 0.5px; }
</style>
</head>
<body>
  <section class="card card-front">
    <div class="wordmark">Pexla</div>
    <div class="details">
      <div class="identity">
        <div class="name">Marcus Dale</div>
        <div class="role">Founder, Director</div>
      </div>
      <div class="divider"></div>
      <ul class="contacts">
        <li>
          <svg viewBox="0 0 16 16" aria-hidden="true"><path d="M4 1.5 6.2 4.3 5 5.8c.8 1.9 2.3 3.4 4.2 4.2l1.5-1.2 2.8 2.2-1.3 2.4C7 13.2 2.8 9 1.6 3z" fill="var(--ink)"/></svg>
          +61 (0)412 555 019
        </li>
        <li>
          <svg viewBox="0 0 16 16" aria-hidden="true"><rect x="1" y="3" width="14" height="10" rx="1" fill="var(--ink)"/><path d="M1.5 3.5 8 9l6.5-5.5" stroke="#fff" stroke-width="1.3" fill="none"/></svg>
          marcus@pexlamedia.com.au
        </li>
        <li>
          <svg viewBox="0 0 16 16" aria-hidden="true"><circle cx="8" cy="8" r="6.5" fill="none" stroke="var(--ink)" stroke-width="1.4"/><ellipse cx="8" cy="8" rx="2.8" ry="6.5" fill="none" stroke="var(--ink)" stroke-width="1.2"/><path d="M1.5 8h13M2.7 4.8h10.6M2.7 11.2h10.6" stroke="var(--ink)" stroke-width="1.1"/></svg>
          www.pexlamedia.com.au
        </li>
      </ul>
    </div>
  </section>

  <section class="card card-back" role="img" aria-label="Navy card back with a faint repeated name pattern, name and web address">
    <div class="wordmark">Pexla</div>
    <div class="site">www.pexlamedia.com.au</div>
  </section>
</body>
</html>
```